Alterations to existing business card

Here is my current logo and I want the "cafe and bar" taken off with just the words Lumo and our slogan "Taste the glow" on the card, Plus the logo.
Our Current Business Card is currently 5.5cm by 5.5cm and would like it to remain like this thanks.
The loyalty card can be 10 squares with the logo specifying the 10th coffee free. I would like the cheapest option please.
Also on our business card would like the Facebook logo and instagram Logo with TAZALUMO27 as link to our photos on instagram.

Keep Colour schemes the same please.

On the business cards

Dale Brinton Director
0427916038
dale27lumo@mailvista.test

Paula Ferrisi Principal
0428571963
paulumo@mailvista.test

Thanks Dale

Industry/Entity Type

Business

```html
<!DOCTYPE html>
<html lang="en">
<head>
<meta charset="utf-8">
<title>Lumo – Business Card &amp; Loyalty Card</title>
<link rel="stylesheet" href="https://fonts.googleapis.com/css2?family=Hind:wght@400;600&display=swap">
<style>
  :root {
    --backdrop: #ecebe8;
    --gold-light: #fbe984;
    --gold-mid: #f2c64e;
    --gold-deep: #e8a732;
    --gold-ring: #e3ae3a;
    --ink: #111111;
    --card-white: #ffffff;
    --stamp-ring: #edc35a;
    --stamp-fill: #fdf6e2;
  }
  * { box-sizing: border-box; margin: 0; padding: 0; }
  html, body { width: 1200px; height: 900px; overflow: hidden; }
  body {
    background: var(--backdrop);
    font-family: "Hind", Arial, sans-serif;
    color: var(--ink);
    position: relative;
  }
  .card {
    position: absolute;
    box-shadow: 0 2px 10px rgba(0,0,0,0.12);
  }
  /* Contact side */
  .card-contact {
    left: 248px; top: 70px; width: 325px; height: 325px;
    background: radial-gradient(circle at 50% 48%, var(--gold-light) 0%, var(--gold-mid) 45%, var(--gold-deep) 100%);
    text-align: center;
    padding-top: 50px;
  }
  .person { margin-bottom: 28px; }
  .person-name { font-weight: 600; font-size: 17px; line-height: 22px; }
  .person-role { font-size: 15px; line-height: 20px; margin-bottom: 9px; }
  .contact-line {
    font-size: 15px; line-height: 20px;
    display: flex; justify-content: center; align-items: center; gap: 7px;
  }
  .contact-line svg { flex: none; }
  .social-links {
    display: flex; justify-content: center; gap: 9px; margin-top: -14px;
  }
  .social-dot {
    width: 25px; height: 25px; border-radius: 50%;
    background: var(--ink); border: 2px solid #fff8d8;
  }
  /* Loyalty side */
  .card-loyalty {
    left: 644px; top: 447px; width: 326px; height: 325px;
    background: var(--card-white);
    text-align: center;
    padding-top: 20px;
  }
  .brand-mark {
    width: 86px; height: 86px; margin: 0 auto;
    border-radius: 50%;
    border: 3px solid var(--gold-ring);
  }
  .brand-name {
    font-size: 30px; font-weight: 400; letter-spacing: 1px;
    line-height: 30px; margin-top: 14px;
  }
  .brand-slogan {
    font-size: 9px; letter-spacing: 1px; color: var(--gold-ring);
    line-height: 12px; text-transform: uppercase;
  }
  .stamp-grid {
    display: grid; grid-template-columns: repeat(5, 40px);
    column-gap: 9px; row-gap: 20px;
    justify-content: center; margin-top: 30px;
  }
  .stamp {
    width: 40px; height: 40px; border-radius: 50%;
    border: 3px solid var(--stamp-ring);
    background: var(--stamp-fill);
    display: flex; align-items: center; justify-content: center;
    font-size: 11px; line-height: 1; padding-top: 2px;
  }
  .stamp-free { background: var(--card-white); }
</style>
</head>
<body>

<section class="card card-contact" aria-label="Business card contact side">
  <div class="person">
    <p class="person-name">Dale Brinton</p>
    <p class="person-role">Director</p>
    <p class="contact-line">
      <svg width="11" height="11" viewBox="0 0 24 24"><path fill="#111" d="M6.6 10.8a15.1 15.1 0 0 0 6.6 6.6l2.2-2.2c.3-.3.7-.4 1-.2 1.1.4 2.3.6 3.6.6.6 0 1 .4 1 1V20c0 .6-.4 1-1 1A17 17 0 0 1 3 4c0-.6.4-1 1-1h3.5c.6 0 1 .4 1 1 0 1.3.2 2.5.6 3.6.1.3 0 .7-.2 1z"/></svg>
      0427916038
    </p>
    <p class="contact-line">
      <svg width="10" height="8" viewBox="0 0 20 16"><path fill="#111" d="M0 0h20v16H0z"/><path d="M1 1l9 7 9-7" fill="none" stroke="#f2c64e" stroke-width="1.6"/></svg>
      dale27lumo@mailvista.test
    </p>
  </div>
  <div class="person">
    <p class="person-name">Paula Ferrisi</p>
    <p class="person-role">Principal</p>
    <p class="contact-line">
      <svg width="11" height="11" viewBox="0 0 24 24"><path fill="#111" d="M6.6 10.8a15.1 15.1 0 0 0 6.6 6.6l2.2-2.2c.3-.3.7-.4 1-.2 1.1.4 2.3.6 3.6.6.6 0 1 .4 1 1V20c0 .6-.4 1-1 1A17 17 0 0 1 3 4c0-.6.4-1 1-1h3.5c.6 0 1 .4 1 1 0 1.3.2 2.5.6 3.6.1.3 0 .7-.2 1z"/></svg>
      0428571963
    </p>
    <p class="contact-line">
      <svg width="10" height="8" viewBox="0 0 20 16"><path fill="#111" d="M0 0h20v16H0z"/><path d="M1 1l9 7 9-7" fill="none" stroke="#f2c64e" stroke-width="1.6"/></svg>
      paulumo@mailvista.test
    </p>
  </div>
  <div class="social-links" aria-label="Social media links">
    <span class="social-dot"></span>
    <span class="social-dot"></span>
  </div>
</section>

<section class="card card-loyalty" aria-label="Loyalty card side">
  <div class="brand-mark"></div>
  <p class="brand-name">LUMO</p>
  <p class="brand-slogan">Taste the glow</p>
  <div class="stamp-grid">
    <span class="stamp"></span><span class="stamp"></span><span class="stamp"></span><span class="stamp"></span><span class="stamp"></span>
    <span class="stamp"></span><span class="stamp"></span><span class="stamp"></span><span class="stamp"></span><span class="stamp stamp-free">FREE</span>
  </div>
</section>

</body>
</html>
```